Business Card and Letterhead for Pimlu - modern real estate business

I need a double sided business card design for Pimlu. Please see business card brief here https://files.trelvonadocs.com/sheet/r/7QzTmWbaXLJnoPEd-kRyUgFhHsstbvCe2qfoMxDa_pz/view?mode=shared

Please feel free to design the business cards however you feel best. I am happy to give some creative freedoms and then provide feedback from there.

Please then also create a letterhead to match the business card design

Colors

Designer to choose colors to be used in the design.

Requirements
Must have
• Must be a modern, elegant business card which looks very professional

```html
<!DOCTYPE html>
<html lang="en">
<head>
<meta charset="utf-8">
<title>Pimlu Business Card</title>
<link href="https://fonts.googleapis.com/css2?family=Nunito+Sans:wght@400;600;800&display=swap" rel="stylesheet">
<style>
  :root {
    --backdrop: #9b9b9b;
    --paper: #f6f6f6;
    --ink: #2a2a2a;
    --brand-red: #e31b26;
    --card-black: #111111;
  }
  * { margin: 0; padding: 0; box-sizing: border-box; }
  html, body { width: 1200px; height: 969px; overflow: hidden; }
  body {
    background: var(--backdrop);
    font-family: "Nunito Sans", Arial, sans-serif;
    display: flex;
    flex-direction: column;
    align-items: center;
    justify-content: center;
    gap: 48px;
  }
  .card {
    position: relative;
    width: 700px;
    height: 400px;
    border-bottom: 4px solid var(--brand-red);
  }
  .card--front { background: var(--paper); color: var(--ink); }
  .card--back {
    background: var(--card-black);
    display: flex;
    align-items: center;
    justify-content: center;
  }
  .brand-name {
    color: var(--brand-red);
    font-weight: 800;
    letter-spacing: 0.04em;
    text-transform: uppercase;
    line-height: 1;
  }
  .card--front .brand-name {
    position: absolute;
    top: 92px;
    right: 70px;
    font-size: 52px;
  }
  .card--back .brand-name { font-size: 150px; }
  .agent {
    position: absolute;
    left: 70px;
    top: 170px;
    font-size: 15px;
    line-height: 1.45;
  }
  .agent__name {
    color: var(--brand-red);
    font-weight: 800;
    font-size: 30px;
    letter-spacing: 0.03em;
    text-transform: uppercase;
    line-height: 1.1;
    margin-bottom: 2px;
  }
  .office {
    position: absolute;
    right: 70px;
    top: 222px;
    font-size: 15px;
    line-height: 1.45;
  }
  .contact-line { display: flex; align-items: center; gap: 10px; }
  .contact-line svg { width: 14px; height: 14px; flex: none; }
  .indent { padding-left: 24px; }
  .icon { fill: none; stroke: var(--brand-red); stroke-width: 1.6; }
  .icon--solid { fill: var(--brand-red); stroke: none; }
</style>
</head>
<body>
  <section class="card card--front" aria-label="Business card front">
    <div class="brand-name">Pimlu</div>

    <div class="agent">
      <div class="agent__name">Rhett Calder</div>
      <div class="indent">Licenced Real Estate Agent</div>
      <div class="indent">Lic No. 20417382</div>
      <div class="contact-line">
        <svg viewBox="0 0 16 16"><path class="icon--solid" d="M4 1.5l2.2 3-1.3 1.6c.8 1.9 2.4 3.5 4.3 4.3l1.6-1.3 3 2.2-1.2 2.6C7.4 13.8 2.2 8.6 1.4 3z"/></svg>
        <span>0455 318 902</span>
      </div>
      <div class="contact-line">
        <svg viewBox="0 0 16 16"><rect class="icon" x="1.5" y="3.5" width="13" height="9"/><path class="icon" d="M1.5 3.5L8 9l6.5-5.5"/></svg>
        <span>rhett@pimlu.com</span>
      </div>
    </div>

    <div class="office">
      <div class="indent">Lic No. 10063418</div>
      <div class="indent">PO Box 7731</div>
      <div class="indent">Larkfield NSW 2790</div>
      <div class="contact-line">
        <svg viewBox="0 0 16 16"><path class="icon--solid" d="M4 1.5l2.2 3-1.3 1.6c.8 1.9 2.4 3.5 4.3 4.3l1.6-1.3 3 2.2-1.2 2.6C7.4 13.8 2.2 8.6 1.4 3z"/></svg>
        <span>02 4811 3907</span>
      </div>
      <div class="contact-line">
        <svg viewBox="0 0 16 16"><rect class="icon" x="1.5" y="3.5" width="13" height="9"/><path class="icon" d="M1.5 3.5L8 9l6.5-5.5"/></svg>
        <span>info@pimlu.com</span>
      </div>
      <div class="contact-line">
        <svg viewBox="0 0 16 16"><circle class="icon" cx="8" cy="8" r="6.3"/><ellipse class="icon" cx="8" cy="8" rx="2.8" ry="6.3"/><path class="icon" d="M1.7 8h12.6M2.8 4.8h10.4M2.8 11.2h10.4"/></svg>
        <span>www.pimlu.com</span>
      </div>
    </div>
  </section>

  <section class="card card--back" aria-label="Business card back">
    <div class="brand-name">Pimlu</div>
  </section>
</body>
</html>
```